Company director needs a business card design

I am a semi-retired former senior finance executive who sits on a number of public and private company boards and do some consulting work. I work largely with emerging businesses but deal regularly with top end of town lawyers, bankers etc. I need a thoughtful but relatively conservative design which would also resonate with my younger client base. Some colour would be good. Information limited to name, address, office tel, mobile and email.

Finance

```html
<!DOCTYPE html>
<html lang="en">
<head>
<meta charset="utf-8">
<title>Business Card – Jonathan Doe</title>
<link href="https://fonts.googleapis.com/css2?family=Play:wght@400;700&display=swap" rel="stylesheet">
<style>
  :root {
    --page-bg: #e6e6e6;
    --card-bg: #ffffff;
    --frame-line: #1a1a1a;
    --name-grey: #858585;
    --text-grey: #5a5a5a;
    --icon-grey: #5f5f5f;
  }
  html, body {
    margin: 0;
    padding: 0;
    width: 992px;
    height: 1200px;
    overflow: hidden;
    background: var(--page-bg);
    font-family: "Play", sans-serif;
  }
  .canvas {
    position: relative;
    width: 992px;
    height: 1200px;
  }
  .card {
    position: absolute;
    left: 68px;
    top: 378px;
    width: 880px;
    height: 492px;
    background: var(--card-bg);
    border-radius: 14px;
  }
  .card-frame {
    position: absolute;
    left: 26px;
    top: 25px;
    width: 815px;
    height: 443px;
    border: 1.5px solid var(--frame-line);
    border-radius: 22px;
  }
  .card-text {
    position: absolute;
    left: 0;
    width: 868px;
    text-align: center;
    margin: 0;
    white-space: nowrap;
  }
  .holder-name {
    top: 86px;
    font-size: 28px;
    letter-spacing: 1px;
    color: var(--name-grey);
    font-weight: 400;
  }
  .holder-title {
    top: 123px;
    font-size: 16px;
    letter-spacing: 0.4px;
    color: var(--text-grey);
  }
  .phone-line {
    font-size: 22px;
    letter-spacing: 1px;
    color: var(--text-grey);
    display: flex;
    justify-content: center;
    align-items: center;
    gap: 14px;
  }
  .phone-mobile { top: 230px; }
  .phone-office { top: 268px; }
  .phone-line svg { width: 22px; height: 24px; fill: var(--icon-grey); }
  .contact-email {
    top: 349px;
    font-size: 20px;
    letter-spacing: 0.6px;
    color: var(--text-grey);
  }
  .contact-address {
    top: 382px;
    font-size: 20px;
    letter-spacing: 0.6px;
    color: var(--text-grey);
  }
</style>
</head>
<body>
<div class="canvas">
  <div class="card">
    <div class="card-frame"></div>

    <h1 class="card-text holder-name">JONATHAN DOE</h1>
    <p class="card-text holder-title">Managing Director</p>

    <p class="card-text phone-line phone-mobile">
      <svg viewBox="0 0 22 24" aria-hidden="true">
        <path d="M5 1h12a2 2 0 0 1 2 2v18a2 2 0 0 1-2 2H5a2 2 0 0 1-2-2V3a2 2 0 0 1 2-2zm0.8 2.5v15.5h10.4V3.5zM11 20a1 1 0 1 0 0.01 0z"/>
      </svg>
      <span>0012 3456 789</span>
    </p>
    <p class="card-text phone-line phone-office">
      <svg viewBox="0 0 22 24" aria-hidden="true">
        <path d="M5 1h12v20H5zM7 3v2h3V3zm5 0v2h3V3zM7 7v2h3V7zm5 0v2h3V7zM7 11v2h3v-2zm5 0v2h3v-2zM7 15v2h3v-2zm5 0v2h3v-2zM0 21.5h22V24H0z"/>
      </svg>
      <span>0012 3456 789</span>
    </p>

    <p class="card-text contact-email">info@yourmail.com</p>
    <p class="card-text contact-address">Address your Inc 00 2nd Ave Lakeview, NJ xxxxx</p>
  </div>
</div>
</body>
</html>
```